Design and Renovation Company Luxury Business Card

I want to create a luxury business card for a Design and Renovation Firm . We will use our current logo. The company name is 528BUILDA. We do not want anything standard. We need a very unique concept.
Please see uploaded inspiration. I really like the textured paper option. I would like the card to be thick with debossing, and/or embossing options. The logo has orange in it but I would like to see the card with and without the orange. I think the orange may make the company feel less high-end. The goal is to elevate the logo not match its vibe per se of the logo. We want something very unique, not standard at all!
I would like a space for :
Logo,
Name,
Position,
Email,
Office number,
Website Address,
Business Address,
Thank you!
Have fun!
Target Market(s)
Home owners Age 35 +
Industry/Entity Type
Design and Renovation
Contact Information for Business Card
Logo, Name, Position, Email, Office number, Website Address, Business Address,.
Colors
Designer to choose colors to be used in the design.
Requirements
Must have
- A luxury designer feel. Must be black or dark grey but open to other luxury ideas.
Nice to have
- Gold, silver, black embossing or debossing. Textured paper design.
Should not have
- A cheap look and feel.

```html
<!DOCTYPE html>
<html lang="en">
<head>
<meta charset="utf-8">
<title>528BUILDA Business Card</title>
<link rel="stylesheet" href="https://fonts.googleapis.com/css2?family=Roboto:wght@400;700&display=swap">
<style>
  :root {
    --backdrop: #e3e3e3;
    --charcoal: #313131;
    --orange: #e38a1d;
    --white: #ffffff;
    --rule: #d9d9d9;
  }
  * { margin: 0; padding: 0; box-sizing: border-box; }
  html, body {
    width: 1200px; height: 1040px; overflow: hidden;
    background: var(--backdrop);
    font-family: "Roboto", Arial, sans-serif;
  }
  .canvas { position: relative; width: 1200px; height: 1040px; }

  .card {
    position: absolute; left: 285px; width: 640px; height: 367px;
    border-radius: 16px; overflow: hidden;
    box-shadow: 0 3px 6px rgba(0,0,0,.35);
  }
  .card--front { top: 130px; background: var(--charcoal); color: var(--white); }
  .card--back { top: 567px; background: var(--orange); color: var(--white); }

  .company-name {
    position: absolute; font-weight: 700; line-height: 1;
    letter-spacing: 0; color: var(--white);
  }
  .card--front .company-name { right: 42px; top: 50px; font-size: 40px; }
  .card--back .company-name { left: 0; right: 0; top: 140px; text-align: center; font-size: 60px; }

  .person { position: absolute; left: 45px; top: 200px; }
  .person__name { font-size: 24px; font-weight: 700; color: var(--orange); line-height: 1.1; }
  .person__role { font-size: 17px; line-height: 1.3; }

  .divider { position: absolute; left: 45px; right: 42px; top: 255px; height: 1px; background: var(--rule); }

  .contacts { position: absolute; left: 45px; top: 265px; list-style: none; }
  .contacts li { display: flex; align-items: center; gap: 8px; font-size: 17px; line-height: 20px; }
  .contacts svg { width: 13px; height: 13px; flex: none; }

  .address { position: absolute; right: 42px; top: 267px; text-align: right; font-size: 17px; line-height: 20px; font-style: normal; }

  .edge-line { position: absolute; left: 0; right: 0; bottom: 21px; height: 3px; background: var(--white); }
  .edge-band { position: absolute; left: 0; right: 0; bottom: 0; height: 18px; background: var(--orange); }

  .back-site { position: absolute; left: 0; right: 0; top: 308px; text-align: center; font-size: 16px; letter-spacing: 4px; }
</style>
</head>
<body>
<main class="canvas">
  <section class="card card--front" aria-label="Card front">
    <p class="company-name">528BUILDA</p>

    <div class="person">
      <p class="person__name">Owen Carter</p>
      <p class="person__role">President</p>
    </div>

    <div class="divider"></div>

    <ul class="contacts">
      <li>
        <svg viewBox="0 0 24 24" aria-hidden="true"><path fill="#e38a1d" d="M6.6 10.8a15.1 15.1 0 0 0 6.6 6.6l2.2-2.2c.3-.3.7-.4 1-.2 1.1.4 2.3.6 3.6.6.6 0 1 .4 1 1V20c0 .6-.4 1-1 1A17 17 0 0 1 3 4c0-.6.4-1 1-1h3.5c.6 0 1 .4 1 1 0 1.3.2 2.5.6 3.6.1.3 0 .7-.2 1z"/></svg>
        (612) 5390-4418
      </li>
      <li>
        <svg viewBox="0 0 24 24" aria-hidden="true"><rect x="2" y="5" width="20" height="14" fill="#e38a1d"/><path d="M2 5l10 8 10-8" fill="none" stroke="#313131" stroke-width="2"/></svg>
        name@528BUILDA.com
      </li>
      <li>
        <svg viewBox="0 0 24 24" aria-hidden="true"><circle cx="12" cy="12" r="10" fill="#e38a1d"/><path d="M2 12h20M12 2c3 3 3 17 0 20M12 2c-3 3-3 17 0 20" fill="none" stroke="#313131" stroke-width="1.5"/></svg>
        www.528BUILDA.com
      </li>
    </ul>

    <address class="address">
      4170 Harrow Lane<br>
      Glen Oaks, NY 11004
    </address>

    <div class="edge-line"></div>
    <div class="edge-band"></div>
  </section>

  <section class="card card--back" aria-label="Card back">
    <p class="company-name">528BUILDA</p>
    <p class="back-site">www.528BUILDA.com</p>
  </section>
</main>
</body>
</html>
```